redesign my website bluekeelvoyages.net and make it user friendly

I already have a website, bluekeelvoyages.net, and want a redesign in WordPress with Elementor Pro, using the same text/content. The goal is to improve:

Design quality (colors, fonts, spacing, visual flow)
User experience (easy navigation, clear offers)
Conversion readiness (calls-to-action, trust signals, booking flow)
Technical side (SEO basics, fast speed, full mobile responsiveness)

The site should look modern, clean, fun, engaging, interactive and optimized for speed and usability.

I would like the 11 page to be consolidate dto 6 as follows: Home (main landing, highlights)

Sailboat Trips (all packages, itineraries, pricing)
Boats (fleet details, features, photos)
How It Works (booking process, FAQs, travel info, what to expect)
Blog
Contact Us (form, WhatsApp, phone, etc.)

Target Market(s)

sailboat trip customers for San Blas Islands in Panama

Industry/Entity Type

Travel, Boat Tour Agency

Coding

Coded - Design and coding required

Number of Pages Required

3 page

Font styles to use
Sans Serif
Other font styles liked:
• Oswalg and sans serif

Colors
0054AA
0677BA
7BADD7
CADEEF
E8F1F8
0094D4
00A9DD
6FCCEA
C7EBF8
E9F6FB
FFC000
F8CF3A
FAE287
FDF2CF
FEFAEE
F0912C
F2A743
F7CA91
FBE8D2
FDF5EE

Requirements
Must have
• Home (main landing, highlights) Sailboat Trips (all packages, itineraries, pricing) Boats (fleet details, features, photos) How It Works (booking process, FAQs, travel info, what to expect) Blog (updates, travel tips, inspiration) Contact Us (form, WhatsApp, phone, etc.)
Nice to have
• I want it to look professionla and be very user friendy to entice people to contact me to book boat trips
Should not have
• a store

```html
<!DOCTYPE html>
<html lang="en">
<head>
<meta charset="utf-8">
<title>Blue Keel Voyages – San Blas Sailing</title>
<link rel="stylesheet" href="https://fonts.googleapis.com/css2?family=Oswald:wght@400;500;600&family=Open+Sans:wght@400;600;700&display=swap">
<style>
:root{
  --navy:#1c1f3a;
  --navy-deep:#161a33;
  --cyan:#1aa3d6;
  --cyan-light:#6fccea;
  --sky:#dff3f8;
  --orange:#f07b22;
  --grey-bg:#e3e4e6;
  --text:#333;
  --white:#fff;
}
*{box-sizing:border-box;margin:0;padding:0}
html,body{width:1200px;height:5268px;overflow:hidden}
body{position:relative;background:var(--white);font-family:"Open Sans",Arial,sans-serif;color:var(--text)}
.abs{position:absolute}
.heading{font-family:"Oswald",Arial,sans-serif;font-weight:500;color:var(--navy-deep);text-transform:uppercase;letter-spacing:-.5px;white-space:nowrap}
.heading .accent{color:var(--cyan)}
.heading-rule{position:absolute;width:90px;height:4px;border-radius:2px;background:var(--cyan)}
.btn{position:absolute;display:flex;align-items:center;justify-content:center;gap:8px;border-radius:30px;font-weight:700;font-size:17px;color:var(--white);background:var(--orange)}
.btn .dot{width:14px;height:14px;border-radius:50%;background:var(--white);position:relative}
.btn .dot::after{content:"";position:absolute;left:4px;top:4px;border-left:6px solid var(--orange);border-top:3px solid transparent;border-bottom:3px solid transparent}

/* header */
.site-header{position:absolute;left:0;top:0;width:1200px;height:104px;background:var(--white);z-index:3}
.brand-badge{position:absolute;left:112px;top:16px;width:124px;height:124px;border-radius:50%;background:var(--navy);border:5px solid var(--cyan);z-index:4;display:flex;align-items:center;justify-content:center;text-align:center;font-family:"Oswald",sans-serif;font-weight:500;font-size:15px;color:var(--white);line-height:1.2}
.top-contact{position:absolute;top:8px;display:flex;align-items:center;gap:10px;font-family:"Oswald",sans-serif;font-size:14px;color:var(--navy-deep);line-height:1.2}
.top-contact .ico{width:40px;height:40px;border-radius:50%;background:var(--navy);display:flex;align-items:center;justify-content:center}
.main-nav{position:absolute;top:70px;left:330px;width:760px;display:flex;justify-content:space-between;font-family:"Oswald",sans-serif;font-size:15px;color:var(--navy-deep)}
.main-nav .active{color:var(--cyan)}

/* hero */
.hero{position:absolute;left:0;top:104px;width:1200px;height:600px;background:linear-gradient(180deg,#7fb6d6 0%,#4e9db5 30%,#2aa0b8 50%,#1787ad 75%,#0e6ea0 100%)}
.hero-title{position:absolute;left:123px;top:266px;font-family:"Oswald",sans-serif;font-weight:500;font-size:40px;line-height:52px;color:var(--white);text-transform:uppercase}

/* discover */
.service-card{position:absolute;top:885px;width:311px;height:335px;border:1px solid #e4e4e4;border-radius:14px;background:var(--white);box-shadow:0 2px 10px rgba(0,0,0,.05);text-align:center;padding:22px 20px 0}
.service-icon{width:108px;height:108px;margin:0 auto 20px;border-radius:50%;background:var(--navy);border:4px solid var(--cyan);display:flex;align-items:center;justify-content:center}
.service-card h3{font-family:"Oswald",sans-serif;font-weight:500;font-size:20px;color:var(--navy-deep);margin-bottom:12px}
.service-card p{font-size:13px;line-height:20.5px;color:#444}

/* about */
.about-bg{position:absolute;left:0;top:1270px;width:1200px;height:678px}
.about-photo{position:absolute;left:110px;top:1343px;width:454px;height:548px;border-radius:44px;background:linear-gradient(160deg,#4cc0da,#2a9fc8 50%,#8fd6e4);overflow:hidden}
.about-photo .corner{position:absolute;left:-70px;bottom:-70px;width:270px;height:270px;border-radius:50%;background:var(--white);display:flex;align-items:center;justify-content:center;padding:50px 0 0 60px;font-family:"Oswald",sans-serif;font-size:17px;color:var(--cyan)}
.about-text{position:absolute;left:619px;top:1537px;width:475px;font-size:14px;line-height:28px;color:#333}

/* fleet */
.fleet-bg{position:absolute;left:0;top:2126px;width:1200px;height:803px;background:linear-gradient(180deg,#fff 0%,#e8f4f6 12%,#3fb1bd 45%,#1a8aa1 70%,#0f5f7e 100%)}
.boat-card{position:absolute;top:2140px;width:311px;height:440px;background:var(--white);border-radius:14px;box-shadow:0 3px 12px rgba(0,0,0,.15);padding:10px}
.boat-photo{height:210px;border-radius:10px;background:linear-gradient(180deg,#5ab5d8,#2fb7c2 55%,#1a8fb0)}
.boat-specs{position:relative;margin:-16px auto 0;width:250px;height:30px;border-radius:16px;background:var(--white);box-shadow:0 1px 5px rgba(0,0,0,.15);display:flex;align-items:center;justify-content:center;gap:14px;font-size:12px;font-weight:600;color:#333}
.boat-row{display:flex;justify-content:space-between;align-items:center;margin:12px 12px 8px}
.boat-row h3{font-family:"Oswald",sans-serif;font-weight:500;font-size:21px;color:var(--navy-deep)}
.boat-row span{font-size:11px;color:var(--orange);font-weight:600}
.boat-card h4{text-align:center;font-size:13px;font-weight:700;color:#222;margin-bottom:4px}
.boat-card p{text-align:center;font-size:12.5px;line-height:20px;color:#333;padding:0 8px}
.boat-btn{position:absolute;left:50%;transform:translateX(-50%);bottom:-14px;width:148px;height:38px;border-radius:20px;background:var(--navy);color:var(--white);font-size:14px;font-weight:600;display:flex;align-items:center;justify-content:center}
.boat-btn.hot{background:var(--orange)}
.arrow-btn{position:absolute;width:38px;height:38px;border-radius:50%;display:flex;align-items:center;justify-content:center}

/* testimonial */
.review{position:absolute;left:163px;top:3170px;width:860px;height:350px;border:1px solid #ddd;border-radius:175px;background:var(--white);box-shadow:0 3px 12px rgba(0,0,0,.06)}
.review-photo{position:absolute;left:30px;top:30px;width:290px;height:290px;border-radius:50%;background:linear-gradient(160deg,#9ccbe6,#3e8fb8 50%,#1d6c93)}
.review-body{position:absolute;left:360px;top:34px;width:455px;font-size:12.5px;line-height:20px;color:#444}
.review-body h3{font-family:"Open Sans",sans-serif;font-size:20px;font-weight:600;color:#222;margin-bottom:4px}
.stars{color:var(--orange);font-size:22px;letter-spacing:3px;margin-bottom:12px}
.review-body p{margin-bottom:18px}

/* booking */
.booking-bg{position:absolute;left:0;top:3560px;width:1200px;height:1200px}
.form-panel{position:absolute;left:110px;top:3761px;width:980px;height:869px;background:var(--navy);border-radius:34px}
.field{position:absolute;height:57px;border-radius:29px;background:var(--white);display:flex;align-items:center;padding:0 24px;font-size:16px;color:#333}
.field.select{justify-content:space-between;padding:0 18px}
.radio,.check{position:absolute;display:flex;align-items:center;gap:12px;font-size:16px;color:var(--white)}
.radio i{width:18px;height:18px;border-radius:50%;border:2px solid var(--white)}
.check i{width:15px;height:15px;border:2px solid var(--white);border-radius:2px}

/* footer */
.footer-bg{position:absolute;left:0;top:4700px;width:1200px;height:568px}
.footer-col h4{font-family:"Oswald",sans-serif;font-weight:500;font-size:20px;color:var(--white);text-transform:uppercase}
.foot-links{position:absolute;font-size:15px;line-height:26px;color:var(--white)}
.foot-contact{position:absolute;left:764px;display:flex;align-items:center;gap:12px;font-family:"Oswald",sans-serif;font-size:14px;color:var(--white);line-height:1.2}
.foot-contact .ico{width:42px;height:42px;border-radius:50%;border:2px solid var(--white);display:flex;align-items:center;justify-content:center}
.social{position:absolute;top:5110px;width:34px;height:34px;border-radius:50%;background:var(--white)}
</style>
</head>
<body>

<!-- header -->
<header class="site-header">
  <div class="top-contact" style="left:690px">
    <div class="ico"><svg width="18" height="18" viewBox="0 0 24 24"><path fill="#fff" d="M6.6 10.8a15.1 15.1 0 0 0 6.6 6.6l2.2-2.2c.3-.3.7-.4 1-.2 1.1.4 2.3.6 3.6.6.6 0 1 .4 1 1V20c0 .6-.4 1-1 1A17 17 0 0 1 3 4c0-.6.4-1 1-1h3.5c.6 0 1 .4 1 1 0 1.3.2 2.5.6 3.6.1.3 0 .7-.2 1z"/></svg></div>
    <div>Whatsup:<br>+573005550142</div>
  </div>
  <div class="top-contact" style="left:876px">
    <div class="ico"><svg width="18" height="14" viewBox="0 0 24 18"><path fill="#fff" d="M2 0h20a2 2 0 0 1 2 2v14a2 2 0 0 1-2 2H2a2 2 0 0 1-2-2V2a2 2 0 0 1 2-2zm10 9 10-6.5V2H2v.5z"/></svg></div>
    <div>Email Us:<br>hello@bluekeelvoyages.net</div>
  </div>
  <nav class="main-nav">
    <span class="active">Home</span><span>Sailboat Trips</span><span>Boats</span><span>How It Works</span><span>Blog</span><span>Contact Us</span>
  </nav>
</header>
<div class="brand-badge">Blue Keel<br>Voyages</div>

<!-- hero -->
<section class="hero" role="img" aria-label="Tropical San Blas island beach with palm trees and turquoise water"></section>
<h1 class="hero-title">San Blas Islands:<br>Panama Sailing Vacations.<br>Ultimate Beaches &amp; Catamaran Tours</h1>
<div class="btn" style="left:123px;top:440px;width:202px;height:53px">Inquire Now <span class="dot"></span></div>
<svg class="abs" style="left:0;top:560px" width="1200" height="160" viewBox="0 0 1200 160">
  <path d="M0 80 C300 140 800 60 1200 90 L1200 160 L0 160Z" fill="var(--cyan)"/>
  <path d="M0 100 C300 160 800 80 1200 110 L1200 160 L0 160Z" fill="#fff"/>
</svg>

<!-- discover -->
<h2 class="heading abs" style="left:0;width:1200px;text-align:center;top:776px;font-size:37px">Discover Ultimate <span class="accent">Panama Sailing Tours</span></h2>
<div class="heading-rule" style="left:555px;top:840px"></div>

<div class="service-card" style="left:108px">
  <div class="service-icon"><svg width="54" height="54" viewBox="0 0 54 54" fill="none" stroke="#fff" stroke-width="2.5"><path d="M26 6v34M26 10 40 36H26M26 16 14 36h12M8 42h38l-5 6H13z"/></svg></div>
  <h3>PRIVATE CHARTERS</h3>
  <p>Sail the beautiful islands and beaches of San Blas on a private all-inclusive catamaran. Enjoy a custom itinerary, friendly crew, and flexible options to fit any budget—perfect for a relaxing escape.</p>
</div>
<div class="service-card" style="left:444px">
  <div class="service-icon"><svg width="54" height="54" viewBox="0 0 54 54" fill="none" stroke="#fff" stroke-width="2.5"><path d="M27 6v8M19 14h16v10H19zM13 24h28l4 12H9zM6 42h42"/></svg></div>
  <h3>SHARED CHARTERS</h3>
  <p>Share the experience with others for a more affordable alternative to a private charter. Perfect for couples, solo travelers, and small groups—enjoy San Blas beaches, clear waters, great meals, and a relaxed</p>
</div>
<div class="service-card" style="left:779px">
  <div class="service-icon"><svg width="58" height="54" viewBox="0 0 58 54" fill="none" stroke="#fff" stroke-width="2.5"><path d="M6 32h46l-6 8H12zM14 32l4-10h22l6 10M22 26h4M30 26h4M6 46h46"/></svg></div>
  <h3>FAMILY FRIENDLY BOAT TRIPS</h3>
  <p>San Blas is perfect for kids, with calm waters, safe snorkeling, and fun island-hopping. Families love the mix of adventure and culture—an ideal way to explore Panama together.</p>
</div>

<!-- about -->
<svg class="about-bg" viewBox="0 0 1200 678" preserveAspectRatio="none"><path d="M0 10 C250 70 450 90 700 60 C900 30 1050 -10 1200 30 L1200 678 L0 678Z" fill="var(--grey-bg)"/></svg>
<div class="about-photo" role="img" aria-label="Snorkeler underwater among striped tropical fish">
  <div class="corner">Blue Keel</div>
</div>
<h2 class="heading abs" style="left:619px;top:1441px;font-size:37px">About Us</h2>
<div class="heading-rule" style="left:621px;top:1503px"></div>
<p class="about-text">We’re sailors and travelers with a love for exploration. When we first arrived in San Blas, its unique beauty and culture left a lasting impression. What began as a stop along our journey soon became something more—we felt a strong connection to this place and a sincere respect for its people, traditions, and way of life. Rather than simply making it our home, we’ve done our best to live in harmony with the environment and the values of the local community. Today, our mission is to share the experience of San Blas with others through safe,</p>
<div class="btn" style="left:616px;top:1819px;width:193px;height:53px">Read More <span class="dot"></span></div>

<!-- fleet -->
<h2 class="heading abs" style="left:0;width:1200px;text-align:center;top:2031px;font-size:37px">Featured <span class="accent">Catamarans</span></h2>
<div class="fleet-bg" role="img" aria-label="Aerial view of a catamaran anchored in turquoise Caribbean water near an island"></div>
<div class="heading-rule" style="left:555px;top:2095px"></div>
<div class="arrow-btn" style="left:52px;top:2322px;background:#bbb"><svg width="12" height="14" viewBox="0 0 12 14"><path d="M9 1 3 7l6 6" stroke="#fff" stroke-width="2" fill="none"/></svg></div>
<div class="arrow-btn" style="left:1106px;top:2322px;background:#111"><svg width="12" height="14" viewBox="0 0 12 14"><path d="M3 1l6 6-6 6" stroke="#fff" stroke-width="2" fill="none"/></svg></div>

<div class="boat-card" style="left:108px">
  <div class="boat-photo" role="img" aria-label="Catamaran near a white sand beach"></div>
  <div class="boat-specs"><span>42 ft</span>|<span>3 cabin</span>|<span>8 Guest</span></div>
  <div class="boat-row"><h3>CORSA 42</h3><span>CATAMARAN</span></div>
  <h4>Service that exceeds all expectations!</h4>
  <p>“We started as strangers and left as friends! The crew made sure everyone felt welcome, and every moment was filled with fun and laughter.”</p>
  <div class="boat-btn">Info &amp; Price</div>
</div>
<div class="boat-card" style="left:444px">
  <div class="boat-photo" role="img" aria-label="Small palm island surrounded by reef"></div>
  <div class="boat-specs"><span>55 ft</span>|<span>4 Cabin</span>|<span>8 Guest</span></div>
  <div class="boat-row"><h3>MARINA 55F</h3><span>CATAMARAN</span></div>
  <h4>Luxury and elegance on water!</h4>
  <p>“It was like having our own private island, but with the luxury of a floating home. Every detail was taken care of, and we felt like VIPs the entire time!”</p>
  <div class="boat-btn hot">Info &amp; Price</div>
</div>
<div class="boat-card" style="left:779px">
  <div class="boat-photo" role="img" aria-label="Catamaran deck from above on blue water"></div>
  <div class="boat-specs"><span>20 ft</span>|<span>3 cabin</span>|<span>9 Guest</span></div>
  <div class="boat-row"><h3>MARINA 55S</h3><span>CATAMARAN</span></div>
  <h4>Safest family fun at sea!</h4>
  <p>“The best family trip we’ve ever had! Our kids couldn’t get enough of exploring the islands. It was the perfect mix of adventure and relaxation.”</p>
  <div class="boat-btn">Info &amp; Price</div>
</div>

<!-- testimonials -->
<h2 class="heading abs" style="left:0;width:1200px;text-align:center;top:3065px;font-size:37px">What They <span class="accent">Say</span></h2>
<div class="heading-rule" style="left:555px;top:3129px"></div>
<div class="review">
  <div class="review-photo" role="img" aria-label="Guests swimming beside a catamaran"></div>
  <div class="review-body">
    <h3>JHONE DEO</h3>
    <div class="stars">★★★★☆</div>
    <p>Everything was absolutely great — from the transfer to the boat crew, the food, and the islands we visited. We really enjoyed the whole experience. The only thing we regret is not having more time to extend the trip in San Blas.</p>
    <p>We booked the Aurelia, the boat is spacious and very confortable.</p>
    <p>The captain Mateo and the chef Elena. Were very professional, friendly and have a lot of knowledge of the San Blas and sailing. They took good care of us and made the trip even better.</p>
  </div>
</div>
<div class="arrow-btn" style="left:143px;top:3324px;background:var(--cyan);width:36px;height:36px"><svg width="10" height="12" viewBox="0 0 12 14"><path d="M9 1 3 7l6 6" stroke="#fff" stroke-width="2" fill="none"/></svg></div>
<div class="arrow-btn" style="left:1006px;top:3324px;background:var(--cyan);width:36px;height:36px"><svg width="10" height="12" viewBox="0 0 12 14"><path d="M3 1l6 6-6 6" stroke="#fff" stroke-width="2" fill="none"/></svg></div>

<!-- booking -->
<svg class="booking-bg" viewBox="0 0 1200 1200" preserveAspectRatio="none"><path d="M0 60 C200 -10 400 20 650 70 C900 120 1050 90 1200 40 L1200 1200 L0 1200Z" fill="var(--sky)"/></svg>
<h2 class="heading abs" style="left:110px;top:3648px;font-size:37px">Book An <span class="accent">Adventure</span></h2>
<div class="heading-rule" style="left:112px;top:3710px"></div>

<div class="form-panel"></div>
<div class="field" style="left:141px;top:3792px;width:436px">Name</div>
<div class="field" style="left:623px;top:3792px;width:438px">Email</div>
<div class="field" style="left:141px;top:3873px;width:920px">Whatsapp Number</div>
<div class="radio" style="left:164px;top:3944px"><i></i>Private Charter</div>
<div class="radio" style="left:344px;top:3944px"><i></i>Shared Charter</div>
<div class="field select" style="left:141px;top:3997px;width:288px">Number of Passengers <span>⬍</span></div>
<div class="field select" style="left:460px;top:3997px;width:286px">Number of Days <span>⬍</span></div>
<div class="field select" style="left:779px;top:3997px;width:282px">Date
  <svg width="16" height="16" viewBox="0 0 16 16"><rect x="1" y="3" width="14" height="12" rx="1" fill="none" stroke="#555" stroke-width="1.6"/><path d="M1 7h14M5 1v4M11 1v4" stroke="#555" stroke-width="1.6"/></svg></div>
<div class="field" style="left:141px;top:4080px;width:920px">What type of experience are you looking for? (Check all that apply)</div>
<div class="check" style="left:170px;top:4165px"><i></i>Relaxing and disconnected</div>
<div class="check" style="left:170px;top:4199px"><i></i>Island-hopping adventure</div>
<div class="check" style="left:170px;top:4233px"><i></i>Snorkeling &amp; marine life</div>
<div class="check" style="left:170px;top:4267px"><i></i>Cultural exchange with the Guna people</div>
<div class="check" style="left:170px;top:4301px"><i></i>Family-friendly</div>
<div class="check" style="left:589px;top:4165px"><i></i>Romantic getaway</div>
<div class="check" style="left:589px;top:4199px"><i></i>Food &amp; drink-focused</div>
<div class="check" style="left:589px;top:4233px"><i></i>Sailing-focused</div>
<div class="check" style="left:589px;top:4267px"><i></i>Budget-friendly</div>
<div class="check" style="left:589px;top:4301px"><i></i>Luxury experience</div>
<div class="field" style="left:141px;top:4358px;width:920px;height:162px;border-radius:28px;align-items:flex-start;padding-top:18px">Message</div>
<div class="btn" style="left:503px;top:4546px;width:192px;height:53px">Send Now <span class="dot"></span></div>

<!-- footer -->
<svg class="footer-bg" viewBox="0 0 1200 568" preserveAspectRatio="none">
  <path d="M0 40 C300 0 800 80 1200 10 L1200 568 L0 568Z" fill="var(--cyan)"/>
  <path d="M0 60 C300 20 800 100 1200 30 L1200 568 L0 568Z" fill="var(--navy)"/>
</svg>
<div class="abs" style="left:112px;top:5120px;width:226px;text-align:center;font-family:'Oswald',sans-serif;font-weight:500;font-size:25px;color:var(--white);white-space:nowrap">Blue Keel Voyages</div>

<div class="footer-col abs" style="left:431px;top:4924px"><h4>Quick Links</h4></div>
<div class="foot-links" style="left:433px;top:4984px">Home<br>Sailboat Trips<br>Boats</div>
<div class="foot-links" style="left:580px;top:4984px">How It Works<br>Blog<br>Contact Us</div>

<div class="footer-col abs" style="left:764px;top:4924px"><h4>Get In Touch</h4></div>
<div class="foot-contact" style="top:4987px">
  <div class="ico"><svg width="16" height="16" viewBox="0 0 24 24"><path fill="#fff" d="M6.6 10.8a15.1 15.1 0 0 0 6.6 6.6l2.2-2.2c.3-.3.7-.4 1-.2 1.1.4 2.3.6 3.6.6.6 0 1 .4 1 1V20c0 .6-.4 1-1 1A17 17 0 0 1 3 4c0-.6.4-1 1-1h3.5c.6 0 1 .4 1 1 0 1.3.2 2.5.6 3.6.1.3 0 .7-.2 1z"/></svg></div>
  <div>Whatsup:<br>+573005550142</div>
</div>
<div class="foot-contact" style="top:5050px">
  <div class="ico"><svg width="16" height="12" viewBox="0 0 24 18"><path fill="#fff" d="M2 0h20a2 2 0 0 1 2 2v14a2 2 0 0 1-2 2H2a2 2 0 0 1-2-2V2a2 2 0 0 1 2-2zm10 9 10-6.5V2H2v.5z"/></svg></div>
  <div>Email Us:<br>hello@bluekeelvoyages.net</div>
</div>
<div class="social" style="left:771px" aria-label="Social profile"></div>
<div class="social" style="left:814px" aria-label="Social profile"></div>
<div class="social" style="left:857px" aria-label="Social profile"></div>

<div class="abs" style="left:112px;top:5190px;width:976px;height:1px;background:rgba(255,255,255,.15)"></div>
<div class="abs" style="left:116px;top:5208px;font-size:14px;color:var(--white)">Copyright 2025 Company Name.All Rights Reserved</div>
<div class="abs" style="left:960px;top:5204px;display:flex;align-items:center;gap:10px;font-size:16px;font-weight:600;color:var(--white)">
  <span style="width:26px;height:26px;border-radius:50%;background:#e8e8ee;display:inline-block"></span>English ⌄
</div>

</body>
</html>
```